RWT Fittings Ltd Business Cards

We need a business card with our business logo. We provide window and door installations on high-rises in west coast British Colombia, Canada.

I would like my business information and details on one side of the card, and the other side the company name with logo

Target Market(s)

General Contractors

Industry/Entity Type

Construction

Contact Information for Business Card

one side i want my company name and logo in the dark theme logo that i provided

Requirements
Must have
• Marco Peltieri, 16045518293, RWTFittings@mailbox-demo.com, 1407-5194 Linden Row Burnaby BC, V5H 2K9, Owner & Manager

```html
<!DOCTYPE html>
<html lang="en">
<head>
<meta charset="utf-8">
<title>RWT Fittings Ltd – Business Cards</title>
<link rel="stylesheet" href="https://fonts.googleapis.com/css2?family=Nunito+Sans:wght@400;700&display=swap">
<style>
  :root {
    --page-bg: #d9dadb;
    --card-white: #f4f5f6;
    --navy: #1f2a33;
    --navy-light: #2c3b47;
    --charcoal: #1e1b1c;
    --brand-blue: #3a9bd0;
    --brand-grey: #8f8782;
    --text-light: #eef1f3;
  }
  * { margin: 0; padding: 0; box-sizing: border-box; }
  html, body {
    width: 1200px; height: 900px; overflow: hidden;
    background: var(--page-bg);
    font-family: "Nunito Sans", Arial, sans-serif;
  }
  .stage {
    position: relative; width: 1200px; height: 900px;
    display: flex; justify-content: center; align-items: center; gap: 110px;
  }
  .card {
    position: relative; width: 340px; height: 595px; overflow: hidden;
    box-shadow: 0 12px 30px rgba(0,0,0,.28);
  }
  .card-front { background: var(--navy); }
  .front-shapes { position: absolute; inset: 0; }
  .front-logo {
    position: absolute; top: 120px; left: 0; width: 100%;
    display: flex; align-items: center; justify-content: center; gap: 12px;
  }
  .logo-square { width: 26px; height: 26px; background: var(--brand-blue); flex: none; }
  .logo-name {
    font-weight: 700; font-size: 28px; color: var(--brand-blue); letter-spacing: .5px;
    white-space: nowrap;
  }
  .contact {
    position: absolute; left: 40px; right: 24px; top: 360px; color: var(--text-light);
  }
  .person-name { font-weight: 700; font-size: 22px; color: var(--brand-blue); letter-spacing: .5px; text-transform: uppercase; }
  .person-title { font-size: 17px; margin-bottom: 34px; }
  .contact-line { display: flex; align-items: center; gap: 10px; font-size: 14px; margin-bottom: 10px; }
  .contact-line svg { flex: none; }
  .address { font-size: 15px; line-height: 1.35; margin-top: 30px; padding-left: 28px; }
  .card-back {
    background: var(--charcoal);
    display: flex; align-items: center; justify-content: center; gap: 12px;
  }
</style>
</head>
<body>
<main class="stage">
  <section class="card card-front">
    <svg class="front-shapes" width="340" height="595" viewBox="0 0 340 595">
      <defs>
        <linearGradient id="navyFade" x1="0" y1="0" x2="0" y2="1">
          <stop offset="0" stop-color="#2c3b47"/>
          <stop offset="1" stop-color="#1f2a33"/>
        </linearGradient>
      </defs>
      <rect x="0" y="190" width="340" height="405" fill="url(#navyFade)" role="img" aria-label="Dark high-rise building silhouettes with window grid"/>
      <polygon points="0,0 340,0 340,200 190,330 0,290 0,300 190,342 340,214 340,200" fill="#9aa0a5"/>
      <polygon points="0,300 190,342 340,214 340,224 190,354 0,312" fill="#3a9bd0"/>
      <polygon points="0,0 340,0 340,200 190,330 0,290" fill="#f4f5f6"/>
    </svg>
    <div class="front-logo">
      <span class="logo-square"></span>
      <span class="logo-name">RWT Fittings Ltd</span>
    </div>
    <div class="contact">
      <p class="person-name">Marco Peltieri</p>
      <p class="person-title">Owner &amp; Manager</p>
      <p class="contact-line">
        <svg width="18" height="18" viewBox="0 0 24 24"><path d="M6.6 10.8a15 15 0 0 0 6.6 6.6l2.2-2.2a1 1 0 0 1 1-.25 11.4 11.4 0 0 0 3.6.57 1 1 0 0 1 1 1V20a1 1 0 0 1-1 1A17 17 0 0 1 3 4a1 1 0 0 1 1-1h3.5a1 1 0 0 1 1 1c0 1.250.2 2.45.57 3.57a1 1 0 0 1-.25 1z" fill="#3a9bd0"/></svg>
        604-551-8293
      </p>
      <p class="contact-line">
        <svg width="18" height="14" viewBox="0 0 24 18"><rect x="1" y="1" width="22" height="16" fill="#3a9bd0"/><path d="M1 1l11 9 11-9" stroke="#1f2a33" stroke-width="2" fill="none"/></svg>
        RWTFittings@mailbox-demo.com
      </p>
      <p class="address">1407-5194 Linden Row<br>Burnaby BC, V5H 2K9</p>
    </div>
  </section>

  <section class="card card-back">
    <span class="logo-square"></span>
    <span class="logo-name">RWT Fittings Ltd</span>
  </section>
</main>
</body>
</html>
```